Business Card for Coastal Tundrabridge Advisory

We need a business card for Coastal Tundrabridge Advisory. The company website address is provided below. The company logo is attached. We provide specialized permafrost services to the mining, transportation, and oil & gas industries. The card should be prepared for:
Matthias Korhonen, PhD.
Coastal Tundrabridge Advisory
PO Box 418259
Quillwater, Alaska 99642
Direct: +1-907-555-0143
Email: mkorhonen@tundrabridgeadvisory.example
Website: www.coastaltundrabridgeadvisory.example

```html
<!DOCTYPE html>
<html lang="en">
<head>
<meta charset="utf-8">
<title>Coastal Tundrabridge Advisory – Business Card</title>
<link href="https://fonts.googleapis.com/css2?family=Montserrat:wght@400;600;700&display=swap" rel="stylesheet">
<style>
  :root {
    --backdrop: #9b9b9b;
    --card-light: #ffffff;
    --card-dark: #0f161e;
    --ink: #141a22;
    --ink-soft: #1e242c;
    --reverse: #ffffff;
    --shadow: rgba(0, 0, 0, 0.35);
  }
  * { margin: 0; padding: 0; box-sizing: border-box; }
  html, body {
    width: 1093px;
    height: 1200px;
    overflow: hidden;
    background: var(--backdrop);
    font-family: "Montserrat", Arial, sans-serif;
    color: var(--ink);
  }
  .card {
    position: absolute;
    left: 264px;
    width: 581px;
    border-radius: 15px;
    box-shadow: 1px 3px 4px var(--shadow);
    overflow: hidden;
  }
  .card--front { top: 225px; height: 363px; background: var(--card-light); }
  .card--back  { top: 616px; height: 367px; background: var(--card-dark); }

  .holder { position: absolute; left: 20px; top: 44px; }
  .holder__name { font-size: 19.5px; font-weight: 700; letter-spacing: 0.1px; line-height: 1.2; }
  .holder__title { font-size: 13px; font-weight: 400; margin-top: 1px; }

  .brand-name {
    position: absolute;
    font-weight: 700;
    font-size: 13px;
    letter-spacing: 0.4px;
    white-space: nowrap;
  }
  .card--front .brand-name { right: 26px; top: 50px; color: var(--ink); }

  .contacts { position: absolute; left: 20px; top: 258px; list-style: none; }
  .contacts__item {
    display: flex;
    align-items: center;
    height: 25px;
    font-size: 12.5px;
    color: var(--ink-soft);
  }
  .contacts__icon { width: 16px; height: 16px; margin-right: 8px; flex: none; }

  .address {
    position: absolute;
    left: 386px;
    top: 296px;
    font-size: 13.5px;
    line-height: 17px;
    font-style: normal;
    color: var(--ink-soft);
  }

  .back-pattern {
    position: absolute;
    inset: 0;
    background:
      linear-gradient(135deg, rgba(150,155,160,0.28) 0%, rgba(80,85,92,0.12) 35%, rgba(0,0,0,0) 60%),
      var(--card-dark);
  }
  .card--back .brand-name {
    left: 0; right: 0;
    top: 283px;
    text-align: center;
    color: var(--reverse);
    font-size: 14px;
  }
</style>
</head>
<body>

<section class="card card--front" aria-label="Card front">
  <div class="holder">
    <h1 class="holder__name">Matthias Korhonen, PhD.</h1>
    <p class="holder__title">Managing Director</p>
  </div>

  <p class="brand-name">Coastal Tundrabridge Advisory</p>

  <ul class="contacts">
    <li class="contacts__item">
      <svg class="contacts__icon" viewBox="0 0 16 16" aria-hidden="true">
        <path d="M4 2.5l2 2.2-1.1 1.6c.7 1.6 1.9 2.8 3.5 3.6l1.6-1.1 2.2 2-1.3 2.2C6.6 12.8 3 9.3 2.2 4z" fill="none" stroke="#141a22" stroke-width="1.4" stroke-linejoin="round"/>
        <path d="M9.5 2.5a4 4 0 0 1 4 4M9.5 4.8a1.8 1.8 0 0 1 1.7 1.7" fill="none" stroke="#141a22" stroke-width="1.2" stroke-linecap="round"/>
      </svg>
      +1-907-555-0143
    </li>
    <li class="contacts__item">
      <svg class="contacts__icon" viewBox="0 0 16 16" aria-hidden="true">
        <rect x="2" y="4" width="12" height="8.5" rx="1" fill="#141a22"/>
        <path d="M2.5 4.8L8 9l5.5-4.2" fill="none" stroke="#fff" stroke-width="1"/>
      </svg>
      mkorhonen@tundrabridgeadvisory.example
    </li>
    <li class="contacts__item">
      <svg class="contacts__icon" viewBox="0 0 16 16" aria-hidden="true">
        <circle cx="8" cy="8" r="6.5" fill="#141a22"/>
        <path d="M4 5.5c1.5 0 2 1 1.5 2s.8 1.5.5 3M9.5 2.5c-.5 1.5.5 2 1.5 2.3s1 1.7 2.5 1.7M9 13.5c0-1.5 1-2 2-2.5" fill="none" stroke="#fff" stroke-width="1"/>
      </svg>
      www.coastaltundrabridgeadvisory.example
    </li>
  </ul>

  <address class="address">
    PO Box 418259<br>
    Quillwater, Alaska 99642
  </address>
</section>

<section class="card card--back" aria-label="Card back">
  <div class="back-pattern" role="img" aria-label="Dark background with a faint repeated company name pattern"></div>
  <p class="brand-name">Coastal Tundrabridge Advisory</p>
</section>

</body>
</html>
```